Australian Trucking Company Requires Professional Looking Stationary

We require a professional looking stationary design that incorporates our newly designed logo.

Our business, called "Brell Haulage Contracting", provides contracting work, transport and logistics to business in Western Australia particularly with links to the mining sector.

We are a small business looking to expand and our new logo and our new stationary will help develop our brand image in our market place.

Target Market(s)

Businesses and Corporation with links to the Mining Sector

Industry/Entity Type

Small Business

Requirements
Must have
• The letterhead must have the following details:
The new logo

Text saying: "Brell Holdings Pty Ltd (ACN 582 316 907) ATF The Brell Discretionary Trust T/AS"
"ABN 71 834 209 553"
Address "P.O Box 817 Wattlegrove WA, 6958"
Phone: 08 9352 7140
Email: brellhaul@mailbox-example.com.au

The text on the letterhead should be editable as the details are likely to change in the near future. Provision should be made for a website address all though one isn't available at the moment.

The styling, layout and font text is entirely up to the designer.

```html
<!DOCTYPE html>
<html lang="en">
<head>
<meta charset="utf-8">
<title>Brell Haulage Contracting — Stationery</title>
<link rel="stylesheet" href="https://fonts.googleapis.com/css2?family=Open+Sans:wght@400;600;700&family=Great+Vibes&display=swap">
<style>
  :root{
    --bg:#ededed;
    --paper:#ffffff;
    --charcoal:#4a4a4c;
    --ink:#3a3a3a;
    --muted:#6b6b6b;
    --brand-red:#c8202a;
    --art-light:#d8d8d8;
    --art-dark:#7a7a7a;
  }
  *{box-sizing:border-box;margin:0;padding:0}
  html,body{width:1200px;height:795px;overflow:hidden}
  body{background:var(--bg);font-family:"Open Sans",Arial,sans-serif;color:var(--ink);position:relative}

  /* Letterhead */
  .letterhead{position:absolute;left:60px;top:30px;width:520px;height:735px;background:var(--paper);box-shadow:0 2px 10px rgba(0,0,0,.12)}
  .letterhead__top-band{position:absolute;left:0;top:0;width:100%;height:9px;background:var(--charcoal)}
  .letterhead__bottom-band{position:absolute;left:0;bottom:0;width:100%;height:22px;background:var(--charcoal)}
  .letterhead__brand{position:absolute;left:34px;top:46px;display:flex;align-items:center;gap:10px}
  .brand-art{background:linear-gradient(135deg,var(--art-light),var(--art-dark))}
  .letterhead__brand .brand-art{width:38px;height:30px}
  .brand-name{color:var(--brand-red);font-weight:700;text-transform:uppercase;line-height:1}
  .letterhead__brand .brand-name{font-size:11px;width:118px}
  .letterhead__contact{position:absolute;right:30px;top:36px;width:190px;font-size:6.2px;line-height:1.5;color:var(--muted)}
  .contact-line{display:flex;gap:8px;flex-wrap:wrap}
  .dot{display:inline-block;width:4px;height:4px;border-radius:50%;background:var(--brand-red);margin-right:3px;vertical-align:middle}
  .letterhead__entity{margin-top:4px}
  .letterhead__body{position:absolute;left:100px;top:170px;width:350px;font-size:8.2px;line-height:1.55;color:var(--muted)}
  .salutation{font-weight:700;color:var(--ink);margin-bottom:10px;font-size:8.6px}
  .letterhead__body p{margin-bottom:10px}
  .signature{position:absolute;left:100px;top:560px}
  .signature__script{font-family:"Great Vibes",cursive;font-size:30px;color:var(--ink);line-height:1}
  .signature__role{font-size:8.4px;font-weight:700;color:var(--ink);margin-top:2px}

  /* Business cards */
  .card{position:absolute;width:440px;height:252px;background:var(--paper);box-shadow:0 2px 10px rgba(0,0,0,.12);overflow:hidden}
  .card--front{left:680px;top:440px}
  .card--back{left:680px;top:120px}
  .card--front .brand-art{position:absolute;left:34px;top:60px;width:190px;height:130px}
  .card--front .brand-name{position:absolute;left:246px;top:98px;font-size:21px;width:180px}
  .card__base-band{position:absolute;left:0;bottom:0;width:100%;height:10px;background:var(--charcoal)}

  .card--back .card__brand{position:absolute;left:28px;top:26px;display:flex;align-items:center;gap:10px}
  .card--back .brand-art{width:52px;height:40px}
  .card--back .brand-name{font-size:15px;width:170px}
  .card__person{position:absolute;left:30px;top:104px}
  .card__name{font-size:15px;color:var(--ink)}
  .card__title{font-size:10px;color:var(--muted)}
  .card__info-band{position:absolute;left:0;bottom:0;width:100%;height:86px;background:var(--charcoal);color:#f2f2f2;font-size:10px;line-height:1.7;display:flex;justify-content:space-between;align-items:center;padding:0 30px}
  .info-row{display:flex;align-items:center;gap:7px}
  .info-row svg{flex:none}
</style>
</head>
<body>

<section class="letterhead" aria-label="Letterhead">
  <div class="letterhead__top-band"></div>

  <div class="letterhead__brand">
    <div class="brand-art" role="img" aria-label="Truck illustration from the company mark"></div>
    <div class="brand-name">Brell Haulage Contracting</div>
  </div>

  <div class="letterhead__contact">
    <div class="contact-line"><span><span class="dot"></span>P.O Box 817 Wattlegrove WA, 6958</span></div>
    <div class="contact-line"><span>T 08 9352 7140</span><span><span class="dot"></span>brellhaul@mailbox-example.com.au</span></div>
    <div class="letterhead__entity">Brell Holdings Pty Ltd (ACN 582 316 907)<br>ATF The Brell Discretionary Trust T/AS<br>ABN 71 834 209 553</div>
  </div>

  <div class="letterhead__body">
    <p class="salutation">Lorem Ipsum,</p>
    <p>Cras mattis consectetur purus sit amet fermentum. Etiam porta sem malesuada magna mollis euismod. Integer posuere erat a ante venenatis dapibus posuere velit aliquet. Cras justo odio, dapibus ac facilisis in, egestas eget quam. Aenean eu leo quam. Pellentesque ornare sem lacinia quam venenatis vestibulum.</p>
    <p>Vivamus sagittis lacus vel augue laoreet rutrum faucibus dolor auctor. Donec sed odio dui. Etiam porta sem malesuada magna mollis euismod. Morbi leo risus, porta ac consectetur ac, vestibulum at eros. Nullam id dolor id nibh ultricies vehicula ut id elit.</p>
    <p>Donec id elit non mi porta gravida at eget metus. Fusce dapibus, tellus ac cursus commodo, tortor mauris condimentum nibh, ut fermentum massa justo sit amet risus. Cras justo odio, dapibus ac facilisis in, egestas eget quam.</p>
    <p>Cum sociis natoque penatibus et magnis dis parturient montes, nascetur ridiculus mus. Curabitur blandit tempus porttitor. Aenean lacinia bibendum nulla sed consectetur.</p>
    <p>Cras justo odio, dapibus ac facilisis in, egestas eget quam. Morbi leo risus, porta ac consectetur ac, vestibulum at eros. Integer posuere erat a ante venenatis dapibus posuere velit aliquet.</p>
  </div>

  <div class="signature">
    <div class="signature__script">Your Name</div>
    <div class="signature__role">Company Director</div>
  </div>

  <div class="letterhead__bottom-band"></div>
</section>

<section class="card card--back" aria-label="Business card, contact side">
  <div class="card__brand">
    <div class="brand-art" role="img" aria-label="Truck illustration from the company mark"></div>
    <div class="brand-name">Brell Haulage Contracting</div>
  </div>
  <div class="card__person">
    <div class="card__name">Declan Marsh</div>
    <div class="card__title">President</div>
  </div>
  <div class="card__info-band">
    <div>
      <div class="info-row">
        <svg width="9" height="9" viewBox="0 0 10 10" aria-hidden="true"><path d="M2 1 L4 1 L5 3.5 L3.8 4.4 Q4.8 6.2 6.2 6.6 L7 5.4 L9 6.4 L9 8.4 Q5 9.4 2 6 Q0.6 3.4 2 1 Z" fill="#f2f2f2"/></svg>
        <span>08 9352 7140</span>
      </div>
      <div class="info-row">
        <svg width="9" height="9" viewBox="0 0 10 10" aria-hidden="true"><rect x="0.5" y="2" width="9" height="6.5" fill="#f2f2f2"/><path d="M0.5 2 L5 5.6 L9.5 2" stroke="#4a4a4c" stroke-width="1" fill="none"/></svg>
        <span>brellhaul@mailbox-example.com.au</span>
      </div>
    </div>
    <div class="info-row">
      <svg width="9" height="11" viewBox="0 0 10 12" aria-hidden="true"><path d="M5 0.5 A4 4 0 0 1 9 4.5 C9 7.5 5 11.5 5 11.5 C5 11.5 1 7.5 1 4.5 A4 4 0 0 1 5 0.5 Z" fill="#f2f2f2"/><circle cx="5" cy="4.5" r="1.5" fill="#4a4a4c"/></svg>
      <span>P.O Box 817<br>Wattlegrove WA, 6958</span>
    </div>
  </div>
</section>

<section class="card card--front" aria-label="Business card, brand side">
  <div class="brand-art" role="img" aria-label="Large truck illustration from the company mark"></div>
  <div class="brand-name">Brell Haulage Contracting</div>
  <div class="card__base-band"></div>
</section>

</body>
</html>
```